Business Card Design

I need business cards designed for a new company i have started that makes cakes, particularly themed kids cakes with a really modern design and I would like to have my business cards reflect this. I have attached some photos of cakes I have made and would like some to be used.

Industry/Entity Type

Business

Contact Information for Business Card

Business Name: Tarts and Treats by Maren
Mobile: 0492 815 063
email: maren@tartsandtreatsbymaren.example.au
Instagram: instagram.com/tartsandtreatsbymaren/
Facebook: fb.me/tartsandtreatsbymaren

Colors
e667a6
b768aa
3276b5

Requirements
Must have
• Business Name: Tarts and Treats by Maren
• Mobile: 0492 815 063
• email: maren@tartsandtreatsbymaren.example.au
• Instagram: instagram.com/tartsandtreatsbymaren/
• Facebook: fb.me/tartsandtreatsbymaren
Nice to have
• 2 to 3 pictures of my cakes

```html
<!DOCTYPE html>
<html lang="en">
<head>
<meta charset="utf-8">
<title>Tarts and Treats by Maren – Business Cards</title>
<link rel="stylesheet" href="https://fonts.googleapis.com/css2?family=Lato:wght@400;700&display=swap">
<style>
  :root {
    --backdrop: #ece8e3;
    --card: #ffffff;
    --pink: #e667a6;
    --pink-deep: #d9488f;
    --purple: #b768aa;
    --ink-light: #ffffff;
    --circle-line: #f1c6dc;
  }
  html, body {
    margin: 0;
    width: 1200px;
    height: 950px;
    overflow: hidden;
    background: var(--backdrop);
    font-family: "Lato", sans-serif;
  }
  .card {
    position: absolute;
    left: 250px;
    width: 700px;
    height: 400px;
    background: var(--card);
    box-shadow: 0 4px 16px rgba(0,0,0,0.15);
    overflow: hidden;
  }
  .card--front { top: 55px; }
  .card--back { top: 495px; }

  .band {
    position: absolute;
    left: 0; right: 0;
    top: 45px;
    height: 310px;
    background: linear-gradient(90deg, var(--pink) 0%, #e46fa9 55%, var(--purple) 100%);
  }
  .band__edge {
    position: absolute;
    left: 0; right: 0;
    bottom: 0;
    height: 14px;
    background: linear-gradient(90deg, var(--pink-deep), var(--pink));
  }

  .brand-circle {
    position: absolute;
    width: 260px;
    height: 260px;
    border-radius: 50%;
    background: var(--card);
    border: 3px solid var(--circle-line);
    box-sizing: border-box;
    display: flex;
    align-items: center;
    justify-content: center;
    text-align: center;
  }
  .card--front .brand-circle { left: 415px; top: 70px; }
  .card--back .brand-circle { left: 240px; top: 70px; }
  .brand-name {
    margin: 0;
    width: 190px;
    color: var(--purple);
    font-weight: 700;
    font-size: 27px;
    line-height: 1.2;
  }

  .contact {
    position: absolute;
    left: 40px;
    top: 195px;
    color: var(--ink-light);
  }
  .contact__name {
    margin: 0;
    font-weight: 700;
    font-size: 20px;
    letter-spacing: 1px;
  }
  .contact__role {
    margin: 2px 0 12px;
    font-size: 13px;
  }
  .contact__list {
    list-style: none;
    margin: 0;
    padding: 0;
    font-size: 12.5px;
  }
  .contact__list li {
    display: flex;
    align-items: center;
    gap: 8px;
    height: 20px;
  }
  .icon { width: 12px; height: 12px; flex: none; }
  .icon--plain { background: var(--ink-light); }
</style>
</head>
<body>
  <section class="card card--front">
    <div class="band"><div class="band__edge"></div></div>
    <div class="brand-circle">
      <p class="brand-name">Tarts and Treats by Maren</p>
    </div>
    <div class="contact">
      <h1 class="contact__name">MAREN HOLT</h1>
      <p class="contact__role">CEO/Founder</p>
      <ul class="contact__list">
        <li>
          <svg class="icon" viewBox="0 0 12 12" aria-hidden="true"><rect x="3" y="0.5" width="6" height="11" rx="1.2" fill="none" stroke="#fff" stroke-width="1.2"/><circle cx="6" cy="9.5" r="0.7" fill="#fff"/></svg>
          0492 815 063
        </li>
        <li>
          <svg class="icon" viewBox="0 0 12 12" aria-hidden="true"><rect x="0.6" y="2.5" width="10.8" height="7.5" fill="none" stroke="#fff" stroke-width="1.2"/><path d="M0.8 2.8 L6 7 L11.2 2.8" fill="none" stroke="#fff" stroke-width="1.2"/></svg>
          maren@tartsandtreatsbymaren.example.au
        </li>
        <li><span class="icon icon--plain"></span>tartsandtreatsbymaren</li>
        <li><span class="icon icon--plain"></span>tartsandtreatsbymaren</li>
      </ul>
    </div>
  </section>

  <section class="card card--back">
    <div class="brand-circle">
      <p class="brand-name">Tarts and Treats by Maren</p>
    </div>
  </section>
</body>
</html>
```